Website for software company "velora"

We need a website for our software company/startup named "velora". We are developing several products (currently 3 standard-software products) which are all in different sectors, but all our products are available for Laptops/PC/Mobile Phones/Tablets, ... We do also create custom software and support our customers with consulting to optimize their processes.
We already have a Logo which you can find in the attached files.
We are a young team of 4 members (two founders and 2 employees).

To get an idea of our products -> the first one is a planning software for healthcare organizations (eg. BlueHaven, firebrigade, pharmacy), the second one is a booking software for sport clubs and the third one is a competition software for sports hunting. You see very diverse. Include or ignore this info of our products as you like.

The design has to be a bootstrap 4 (or higher) design. We have licenced FontAwesome as iconset. Responsive design should come without saying.

• Starting page, product pages, news section, contact, team, services

```html
<!DOCTYPE html>
<html lang="en">
<head>
<meta charset="utf-8">
<title>velora – Software for every device</title>
<link href="https://fonts.googleapis.com/css2?family=Montserrat:wght@300;400;500;600;700&display=swap" rel="stylesheet">
<style>
:root{
  --ink:#1f2530;
  --navy:#2b323d;
  --orange:#f07a1f;
  --orange-deep:#e85f1c;
  --grey-bg:#f1f1f1;
  --text:#3d434c;
  --muted:#8a8f96;
  --white:#ffffff;
}
*{box-sizing:border-box;margin:0;padding:0}
html,body{width:1200px;height:3402px;overflow:hidden}
body{font-family:'Montserrat',sans-serif;color:var(--text);background:var(--white);position:relative}
.abs{position:absolute}
a{color:inherit;text-decoration:none}

/* header */
.site-header{position:absolute;left:0;top:0;width:1200px;height:78px;background:var(--white)}
.brand{position:absolute;left:132px;top:18px;font-size:42px;font-weight:700;color:var(--navy);letter-spacing:1px;line-height:42px}
.main-nav a{position:absolute;top:33px;font-size:12px;font-weight:600;color:var(--navy);letter-spacing:.3px}
.main-nav a.active::after{content:"";position:absolute;left:0;right:0;top:22px;height:2px;background:var(--orange)}
.btn-contact{position:absolute;left:958px;top:21px;width:125px;height:37px;border-radius:19px;background:var(--navy);color:var(--white);font-size:12px;font-weight:700;display:flex;align-items:center;justify-content:center}

/* hero */
.hero{position:absolute;left:0;top:78px;width:1200px;height:472px;background:var(--navy);overflow:hidden}
.hero-photo{position:absolute;left:560px;top:0;width:640px;height:472px;background:linear-gradient(100deg,#2b323d 0%,#5b5d5f 35%,#8a8882 70%,#b9b3a8 100%)}
.hero-kicker{position:absolute;left:110px;top:165px;font-size:25px;font-weight:400;color:var(--white)}
.hero-title{position:absolute;left:110px;top:194px;font-size:35px;font-weight:700;color:var(--white)}
.hero-lead{position:absolute;left:113px;top:244px;width:420px;font-size:15.5px;line-height:21px;color:#dfe2e6}

/* product */
.device-mock{border-radius:14px;background:linear-gradient(160deg,#f4f5f7,#dcdfe3)}
.eyebrow{font-size:15px;color:var(--orange);letter-spacing:.5px}
.section-title{font-size:35px;font-weight:400;color:var(--ink);line-height:38px}
.section-title strong{font-weight:700;display:block}
.body-copy{font-size:15px;line-height:23px;color:var(--text)}

/* features */
.features{position:absolute;left:0;top:1049px;width:1200px;height:506px;background:var(--grey-bg)}
.feature-title{font-size:28px;line-height:33px;color:var(--ink);font-weight:400}
.feature-title strong{display:block;font-weight:700}
.tick-list li{list-style:none;position:absolute;left:0;width:420px;font-size:14px;font-weight:600;line-height:21px;color:var(--ink);padding-left:41px}
.tick-list svg{position:absolute;left:0;top:4px}

/* services */
.services{position:absolute;left:0;top:2103px;width:1200px;height:505px;background:var(--navy);overflow:hidden}
.services-floor{position:absolute;left:0;bottom:0;width:1200px;height:200px;background:linear-gradient(180deg,rgba(43,50,61,0),#3a414c)}
.center-title{position:absolute;left:0;width:1200px;text-align:center;font-size:28px;line-height:33px;color:var(--white);font-weight:400}
.center-title strong{display:block;font-weight:700}
.rule{position:absolute;height:3px;background:var(--orange)}
.service-card{position:absolute;top:200px;width:280px;height:131px;background:var(--white)}
.service-card .icon{position:absolute;left:20px;top:25px;width:68px;height:68px;border-radius:50%;display:flex;align-items:center;justify-content:center}
.service-card h3{position:absolute;left:102px;top:30px;font-size:12px;font-weight:700;color:var(--ink);letter-spacing:.5px}
.service-card p{position:absolute;left:102px;top:48px;width:165px;font-size:12px;line-height:17px;color:var(--text)}

/* contact */
.contact{position:absolute;left:0;top:2608px;width:1200px;height:454px;background:linear-gradient(180deg,var(--orange-deep) 0%,#f27a2c 55%,#ec6a22 100%)}
.contact .center-title{top:68px;font-size:29px}
.field{position:absolute;background:var(--white);border:1px solid #f3d2bd;font-size:13px;color:var(--ink);padding:0 16px;display:flex;align-items:center}
.field.message{align-items:flex-start;padding-top:18px;padding-left:24px}
.btn-send{position:absolute;left:517px;top:344px;width:151px;height:42px;border-radius:21px;background:var(--navy);color:var(--white);font-size:12px;font-weight:700;display:flex;align-items:center;justify-content:center}

/* footer */
.site-footer{position:absolute;left:0;top:3062px;width:1200px;height:340px;background:var(--white)}
.footer-brand{position:absolute;left:141px;top:84px;font-size:40px;font-weight:700;color:var(--navy);letter-spacing:1px}
.footer-about{position:absolute;left:138px;top:138px;width:235px;font-size:11px;line-height:15.5px;color:var(--muted)}
.divider{position:absolute;top:0;width:1px;height:251px;background:#e6e7e9}
.divider::after{content:"";position:absolute;left:-1px;top:58px;width:3px;height:22px;background:var(--orange)}
.footer-col h4{position:absolute;top:62px;font-size:13px;font-weight:700;color:var(--ink);letter-spacing:.5px}
.footer-col a{position:absolute;font-size:12.5px;color:var(--text)}
.social{position:absolute;top:95px;width:28px;height:28px;border-radius:50%;background:var(--navy)}
.social.first{background:var(--orange)}
.legal{position:absolute;left:0;top:288px;width:1200px;border-top:1px solid #e6e7e9;text-align:center;padding-top:12px;font-size:10.5px;color:var(--muted)}
</style>
</head>
<body>

<header class="site-header">
  <div class="brand">VELORA</div>
  <nav class="main-nav">
    <a href="#" class="active" style="left:420px">PRODUCT</a>
    <a href="#" style="left:544px">SERVICES</a>
    <a href="#" style="left:668px">NEWS</a>
    <a href="#" style="left:767px">TEAM</a>
    <a href="#" style="left:863px">ABOUT</a>
  </nav>
  <a href="#" class="btn-contact">CONTACT</a>
</header>

<section class="hero">
  <div class="hero-photo" role="img" aria-label="Photo of a person using a tablet with charts and a stylus, with a plant and a mug on the desk"></div>
  <div class="hero-kicker">SED UT PERSPICIATIS</div>
  <h1 class="hero-title">COMPETITION SOFTWARE</h1>
  <p class="hero-lead">Lorem ipsum dolor sit amet, consectetur adipiscing elit, sed do eiusmod tempor incididunt.</p>
</section>

<section class="product">
  <div class="abs device-mock" style="left:129px;top:653px;width:425px;height:308px" role="img" aria-label="Tablet and phone mockups showing the competition software tables"></div>
  <div class="abs eyebrow" style="left:626px;top:657px">PRODUCT&nbsp; TITLE</div>
  <h2 class="abs section-title" style="left:626px;top:682px">COMPETITION<strong>SOFTWARE</strong></h2>
  <p class="abs body-copy" style="left:627px;top:780px;width:470px">Lorem ipsum dolor sit amet, consectetur adipiscing elit, sed do eiusmod tempor incididunt ut laborLorem ipsum dolor sit amet, consectetur adipiscing elit, sed do eiusmoLorem ipsum dolor sit amet, consectetur adipiscing elit, sed do</p>
  <p class="abs body-copy" style="left:627px;top:887px;width:460px">Aiusmod tempor incididunt ut laborLorem ipsum dolor sit amet, consectetur adipiscing elit, sed do eiusmo</p>
</section>

<section class="features">
  <h2 class="abs feature-title" style="left:128px;top:99px">SED UT PERSPICIATIS UNDE<strong>NATUS ERROR SIT</strong></h2>
  <ul class="abs tick-list" style="left:128px;top:187px">
    <li style="top:0">
      <svg width="20" height="20" viewBox="0 0 20 20"><circle cx="10" cy="10" r="10" fill="#f07a1f"/><path d="M5.5 10.3l3 3 6-6" stroke="#fff" stroke-width="2.2" fill="none" stroke-linecap="round" stroke-linejoin="round"/></svg>
      Lorem ipsum dolor sit amet, consectetur adipiscing elit, sed do eiusmod tempor incididunt ut labor</li>
    <li style="top:68px">
      <svg width="20" height="20" viewBox="0 0 20 20"><circle cx="10" cy="10" r="10" fill="#f07a1f"/><path d="M5.5 10.3l3 3 6-6" stroke="#fff" stroke-width="2.2" fill="none" stroke-linecap="round" stroke-linejoin="round"/></svg>
      Lorem ipsum dolor sit amet, consectetur adipiscing elit, sed do eiusmoLorem ipsum dolor sit amet</li>
    <li style="top:136px">
      <svg width="20" height="20" viewBox="0 0 20 20"><circle cx="10" cy="10" r="10" fill="#f07a1f"/><path d="M5.5 10.3l3 3 6-6" stroke="#fff" stroke-width="2.2" fill="none" stroke-linecap="round" stroke-linejoin="round"/></svg>
      Aiusmod tempor incididunt ut laborLorem ipsum dolor sit amet, consectetur adipiscing elit</li>
  </ul>
  <div class="abs" style="left:615px;top:87px;width:452px;height:328px;background:linear-gradient(160deg,#e3e4e7,#f7f7f8)" role="img" aria-label="Dashboard screenshot with user and order counters, bar, line and ring charts"></div>
</section>

<section class="planning">
  <div class="abs device-mock" style="left:139px;top:1633px;width:448px;height:369px" role="img" aria-label="Tablet and phone mockups of the planning interface with statistics and booking cards"></div>
  <h2 class="abs feature-title" style="left:653px;top:1673px;font-size:30px;line-height:34px">EASY PLANNING INTERFACE<strong>NATUS ERROR SIT</strong></h2>
  <p class="abs body-copy" style="left:651px;top:1767px;width:420px">Lorem ipsum dolor sit amet, consectetur adipiscing elit, sed do eiusmod tempor incididunt ut laborLorem ipsumdolor sit amet, consectetur adipiscing elit, sed do eiusmoLorem ipsum dolor sit amet</p>
  <p class="abs body-copy" style="left:651px;top:1887px;width:430px">Aiusmod tempor incididunt ut laborLorem ipsum dolor sit amet, consectetur adipiscing elit</p>
</section>

<section class="services">
  <div class="services-floor" role="img" aria-label="Faint perspective grid floor"></div>
  <h2 class="center-title" style="top:70px">SED UT PERSPICIATIS UNDE<strong>NATUS ERROR SIT</strong></h2>
  <div class="rule" style="left:564px;top:145px;width:74px"></div>

  <article class="service-card" style="left:141px">
    <div class="icon" style="background:var(--navy)">
      <svg width="34" height="30" viewBox="0 0 34 30" fill="none" stroke="#fff" stroke-width="1.6"><rect x="2" y="2" width="30" height="19" rx="1"/><path d="M12 28h10M17 21v7M7 15l5-5 4 3 6-6 5 4"/></svg>
    </div>
    <h3>LOREM IPSUM DOLOR</h3>
    <p>Neque porro quisquam est, qui dolorem ipsum quia dolor sit amet</p>
  </article>
  <article class="service-card" style="left:438px">
    <div class="icon" style="background:var(--orange)">
      <svg width="30" height="30" viewBox="0 0 30 30" fill="none" stroke="#fff" stroke-width="1.6"><rect x="3" y="5" width="24" height="22" rx="2"/><path d="M3 11h24M9 2v6M21 2v6M8 16h3M14 16h3M20 16h3M8 21h3M14 21h3"/></svg>
    </div>
    <h3>LOREM IPSUM DOLOR</h3>
    <p>Neque porro quisquam est, qui dolorem ipsum quia dolor sit amet</p>
  </article>
  <article class="service-card" style="left:726px">
    <div class="icon" style="background:#5d6673">
      <svg width="32" height="32" viewBox="0 0 32 32" fill="none" stroke="#fff" stroke-width="1.6"><circle cx="16" cy="16" r="13"/><circle cx="16" cy="16" r="5"/><path d="M16 3v6M16 23v6M3 16h6M23 16h6"/></svg>
    </div>
    <h3>LOREM IPSUM DOLOR</h3>
    <p>Neque porro quisquam est, qui dolorem ipsum quia dolor sit amet</p>
  </article>
</section>

<section class="contact">
  <h2 class="center-title">CONTACT <strong style="display:inline">VELORA</strong></h2>
  <div class="rule" style="left:549px;top:109px;width:74px;background:var(--white)"></div>
  <div class="field" style="left:213px;top:143px;width:374px;height:50px">Name*</div>
  <div class="field" style="left:213px;top:204px;width:374px;height:51px">Email address*</div>
  <div class="field" style="left:213px;top:264px;width:374px;height:52px">Phone*</div>
  <div class="field message" style="left:598px;top:143px;width:374px;height:173px">Message</div>
  <a href="#" class="btn-send">CONTACT US</a>
</section>

<footer class="site-footer">
  <div class="footer-brand">VELORA</div>
  <p class="footer-about">Lorem ipsum dolor sit amet, consectetur adipiscing elit, sed do eiusmod tempor incididunt ut labore et dolore</p>

  <div class="divider" style="left:422px"></div>
  <div class="divider" style="left:653px"></div>
  <div class="divider" style="left:878px"></div>

  <div class="footer-col">
    <h4 style="left:465px">NAVIGATION</h4>
    <a href="#" style="left:465px;top:96px">About Us</a>
    <a href="#" style="left:465px;top:125px">Products</a>
    <a href="#" style="left:465px;top:154px">Services</a>
    <a href="#" style="left:465px;top:183px">Contact Us</a>
  </div>
  <div class="footer-col">
    <h4 style="left:700px">RESOURCES</h4>
    <a href="#" style="left:701px;top:96px">News</a>
    <a href="#" style="left:701px;top:125px">Team</a>
    <a href="#" style="left:701px;top:154px">Privacy Policy</a>
  </div>
  <div class="footer-col">
    <h4 style="left:909px">FOLLOW US</h4>
    <span class="social first" style="left:909px"></span>
    <span class="social" style="left:943px"></span>
    <span class="social" style="left:977px"></span>
    <span class="social" style="left:1012px"></span>
  </div>

  <div class="legal">© 2022 Velora &nbsp;| All Rights Reserved</div>
</footer>

</body>
</html>
```